Request for Business Card Design

Hi. My name is Marlene, I am looking for a new business card design for my company, Quarrow Signal Instruments, LLC. I really like the design you did for Tarsel Venture and was hoping you could do something similar using our full logo and our mark. I am also open to any raised texture design using our mark. I have attached our full logo, which would need to be somewhere on the card, as well as the mark in both outline and full form, as well as our brand colors / guide. The card does not have to be white, as long as our logo and mark appear. I actually like darker colored business cards more, but am open to all options. If you are interested in working with me, please let me know. We would also take the business card design into letterhead design if you can do that.

```html
<!DOCTYPE html>
<html lang="en">
<head>
<meta charset="utf-8">
<title>Quarrow Signal Instruments – Business Card</title>
<link rel="stylesheet" href="https://fonts.googleapis.com/css2?family=Open+Sans:ital,wght@0,400;0,600;0,700;1,400;1,600;1,700&display=swap">
<style>
  :root {
    --backdrop: #3b3431;
    --card: #ffffff;
    --brand-blue: #0e98bf;
    --ink: #2f2f31;
    --ink-soft: #3c3c3e;
  }
  * { box-sizing: border-box; margin: 0; padding: 0; }
  html, body {
    width: 1200px; height: 716px; overflow: hidden;
    background: var(--backdrop);
    font-family: "Open Sans", Arial, sans-serif;
  }
  .canvas { position: relative; width: 1200px; height: 716px; }

  .card {
    position: absolute;
    top: 208px;
    width: 520px; height: 300px;
    background: var(--card);
    overflow: hidden;
    box-shadow: 0 10px 24px rgba(0,0,0,.45);
  }
  .card--front { left: 64px; }
  .card--back  { left: 616px; }

  .accent-disc {
    position: absolute;
    width: 360px; height: 360px;
    border-radius: 50%;
    background: var(--brand-blue);
  }
  .card--front .accent-disc { left: 372px; top: 86px; }
  .card--back  .accent-disc { left: -180px; top: 86px; }

  .wordmark { display: flex; align-items: center; gap: 10px; }
  .wordmark__dot {
    width: 30px; height: 30px; border-radius: 50%;
    background: var(--brand-blue); flex: none;
  }
  .wordmark__name {
    font-weight: 700; color: var(--ink);
    text-transform: uppercase; line-height: 1.05;
  }

  .card--front .wordmark { position: absolute; left: 30px; top: 26px; }
  .card--front .wordmark__name { font-size: 17px; letter-spacing: 1.5px; }

  .person {
    position: absolute; left: 30px; top: 92px;
    padding-left: 14px;
    border-left: 8px solid var(--brand-blue);
  }
  .person__name {
    font-size: 20px; font-weight: 700; font-style: italic;
    color: var(--brand-blue); text-transform: uppercase; letter-spacing: .3px;
  }
  .person__role { font-size: 13px; color: var(--ink-soft); margin-top: 1px; }

  .address {
    position: absolute; left: 52px; top: 152px;
    font-size: 13px; line-height: 18px; color: var(--ink-soft);
  }
  .contacts {
    position: absolute; left: 30px; top: 202px;
    list-style: none; font-size: 13px; line-height: 19px; color: var(--ink-soft);
  }
  .contacts li { display: flex; align-items: center; gap: 7px; }
  .contacts svg { width: 11px; height: 11px; fill: var(--brand-blue); flex: none; }

  .card--back .wordmark { position: absolute; right: 34px; top: 126px; gap: 14px; }
  .card--back .wordmark__dot { width: 44px; height: 44px; }
  .card--back .wordmark__name { font-size: 22px; letter-spacing: 2px; }
</style>
</head>
<body>
<main class="canvas">

  <section class="card card--front" aria-label="Business card front">
    <div class="accent-disc"></div>
    <div class="wordmark">
      <span class="wordmark__dot"></span>
      <span class="wordmark__name">Quarrow<br>Signal Instruments</span>
    </div>
    <div class="person">
      <p class="person__name">Owen Hartley</p>
      <p class="person__role">Managing Director</p>
    </div>
    <p class="address">Your address, City<br>State, Zip 1234</p>
    <ul class="contacts">
      <li>
        <svg viewBox="0 0 24 24" aria-hidden="true"><path d="M6.6 10.8a15.1 15.1 0 0 0 6.6 6.6l2.2-2.2c.3-.3.7-.4 1-.2 1.1.4 2.3.6 3.6.6.6 0 1 .4 1 1V20c0 .6-.4 1-1 1A17 17 0 0 1 3 4c0-.6.4-1 1-1h3.5c.6 0 1 .4 1 1 0 1.3.2 2.5.6 3.6.1.3 0 .7-.2 1z"/></svg>
        123 456 789
      </li>
      <li>
        <svg viewBox="0 0 24 24" aria-hidden="true"><path d="M2 5h20v14H2zm2 2v.5l8 5 8-5V7l-8 5z"/></svg>
        info@yourgmail.com
      </li>
      <li>
        <svg viewBox="0 0 24 24" aria-hidden="true"><path d="M12 2a10 10 0 1 0 0 20 10 10 0 0 0 0-20zm-1 17.9A8 8 0 0 1 4.1 10.9L9 16v1a2 2 0 0 0 2 2zm6.9-2.5A2 2 0 0 0 16 16h-1v-3a1 1 0 0 0-1-1H8v-2h2a1 1 0 0 0 1-1V7h2a2 2 0 0 0 2-2v-.4a8 8 0 0 1 2.9 12.8z"/></svg>
        www.yourwebsite.com
      </li>
    </ul>
  </section>

  <section class="card card--back" aria-label="Business card back">
    <div class="accent-disc"></div>
    <div class="wordmark">
      <span class="wordmark__dot"></span>
      <span class="wordmark__name">Quarrow<br>Signal Instruments</span>
    </div>
  </section>

</main>
</body>
</html>
```